Business card design for international hub site

I need a business card design with the logo attached. Although the site is for the teenage audience (it is about the high school graduation ball, the Prom), the business card is for professional use to be given to professional contacts (B2B), such as suppliers and partners, so it needs to look professional (but also girly, glamours and clean).

Target Market(s)

B2B

Industry/Entity Type

Media

Colors
eea4c8
f9d9e8
e667a6
9d9d9d
1b1b1b

Requirements
Must have
• Space for Name, Tile, Address, Phone, email and website.
Should not have
• Photo

```html
<!DOCTYPE html>
<html lang="en">
<head>
<meta charset="utf-8">
<title>The Gala Glow – Business Card</title>
<link href="https://fonts.googleapis.com/css2?family=EB+Garamond:wght@400;500&family=Pinyon+Script&display=swap" rel="stylesheet">
<style>
  :root {
    --card-pink: #e6397b;
    --band-white: #ffffff;
    --petal-soft: #f9d9e8;
    --petal-mid: #eea4c8;
    --accent-pink: #e667a6;
    --ink: #1b1b1b;
    --muted: #9d9d9d;
    --stage: #ededed;
  }
  * { margin: 0; padding: 0; box-sizing: border-box; }
  html, body {
    width: 1200px;
    height: 586px;
    overflow: hidden;
    background: var(--stage);
  }
  .stage {
    position: relative;
    width: 1200px;
    height: 586px;
  }
  .card {
    position: absolute;
    top: 126px;
    width: 501px;
    height: 294px;
    overflow: hidden;
  }
  /* Front */
  .card--front {
    left: 61px;
    background: var(--card-pink);
  }
  .front-band {
    position: absolute;
    left: 0;
    top: 209px;
    width: 100%;
    height: 59px;
    background: var(--band-white);
  }
  .front-ornament {
    position: absolute;
    left: 231px;
    top: 128px;
    width: 270px;
    height: 140px;
    border-radius: 60px 0 0 40px;
    background: linear-gradient(135deg, rgba(255,255,255,0.55), rgba(249,217,232,0.35));
  }
  .brand {
    position: absolute;
    left: 36px;
    top: 62px;
    display: flex;
    align-items: center;
    gap: 10px;
    font-family: "EB Garamond", Garamond, serif;
    font-weight: 400;
    font-size: 44px;
    line-height: 1;
    color: var(--band-white);
    white-space: nowrap;
  }
  .brand-dot {
    width: 12px;
    height: 12px;
    border-radius: 50%;
    background: var(--band-white);
  }
  /* Back */
  .card--back {
    left: 619px;
    background: var(--band-white);
  }
  .back-ornament {
    position: absolute;
    left: 0;
    top: 0;
    width: 170px;
    height: 100%;
    background: linear-gradient(90deg, var(--card-pink) 0%, var(--petal-mid) 55%, rgba(249,217,232,0) 100%);
  }
  .back-ornament-faint {
    position: absolute;
    right: 0;
    top: 0;
    width: 120px;
    height: 100%;
    background: linear-gradient(270deg, rgba(249,217,232,0.7), rgba(249,217,232,0));
  }
  .holder-name {
    position: absolute;
    right: 54px;
    top: 58px;
    font-family: "Pinyon Script", cursive;
    font-size: 36px;
    line-height: 1.1;
    color: var(--accent-pink);
    white-space: nowrap;
  }
  .holder-title {
    position: absolute;
    right: 55px;
    top: 102px;
    font-family: "EB Garamond", Garamond, serif;
    font-size: 11px;
    letter-spacing: 1.5px;
    text-transform: uppercase;
    color: var(--muted);
    white-space: nowrap;
  }
  .contact-list {
    position: absolute;
    right: 54px;
    top: 130px;
    list-style: none;
    font-family: "EB Garamond", Garamond, serif;
    font-size: 12.5px;
    color: var(--ink);
  }
  .contact-item {
    display: flex;
    justify-content: flex-end;
    align-items: center;
    gap: 10px;
    height: 22px;
    white-space: nowrap;
  }
  .contact-icon {
    width: 13px;
    height: 11px;
    fill: var(--accent-pink);
    flex: none;
  }
  .address {
    position: absolute;
    right: 55px;
    top: 224px;
    text-align: right;
    font-family: "EB Garamond", Garamond, serif;
    font-size: 13px;
    line-height: 19px;
    color: var(--accent-pink);
    font-style: normal;
    white-space: nowrap;
  }
</style>
</head>
<body>
<main class="stage">

  <section class="card card--front" aria-label="Card front">
    <div class="front-band"></div>
    <div class="front-ornament" role="img" aria-label="White floral swirl ornament"></div>
    <div class="brand">
      <span class="brand-dot"></span>
      <span class="brand-name">the gala glow</span>
    </div>
  </section>

  <section class="card card--back" aria-label="Card back">
    <div class="back-ornament" role="img" aria-label="Pink floral swirl ornament with flowers and leaves"></div>
    <div class="back-ornament-faint" role="img" aria-label="Faint pink floral swirl ornament"></div>

    <p class="holder-name">Mara Lindqvist</p>
    <p class="holder-title">Partnerships Director</p>

    <ul class="contact-list">
      <li class="contact-item">
        <span>+44 (0)1632 960418</span>
        <svg class="contact-icon" viewBox="0 0 13 11" aria-hidden="true">
          <path d="M1 3.5C1 2 3 1 6.5 1S12 2 12 3.5V4.5H9.5V3.3C8.7 3 7.6 2.9 6.5 2.9S4.3 3 3.5 3.3V4.5H1Z"/>
          <rect x="2.5" y="5.5" width="8" height="4.5" rx="1"/>
        </svg>
      </li>
      <li class="contact-item">
        <span>(555) 014-2276</span>
        <svg class="contact-icon" viewBox="0 0 13 11" aria-hidden="true">
          <rect x="3.5" y="0.5" width="6" height="3"/>
          <rect x="0.5" y="4" width="12" height="4.5" rx="1"/>
          <rect x="3.5" y="7.5" width="6" height="3"/>
        </svg>
      </li>
      <li class="contact-item">
        <span>mara@thegalaglow.com</span>
        <svg class="contact-icon" viewBox="0 0 13 11" aria-hidden="true">
          <rect x="0.5" y="1" width="12" height="9"/>
          <path d="M0.8 1.5L6.5 6.3L12.2 1.5" fill="none" stroke="#ffffff" stroke-width="1"/>
        </svg>
      </li>
      <li class="contact-item">
        <span>www.thegalaglow.com</span>
        <svg class="contact-icon" viewBox="0 0 13 11" aria-hidden="true">
          <circle cx="6.5" cy="5.5" r="5"/>
          <path d="M1.5 5.5H11.5M6.5 0.5C4.5 3 4.5 8 6.5 10.5M6.5 0.5C8.5 3 8.5 8 6.5 10.5" fill="none" stroke="#ffffff" stroke-width="0.8"/>
        </svg>
      </li>
    </ul>

    <address class="address">
      Orchard Lane, Hensby<br>
      Kelford, ZZ9 4QT
    </address>
  </section>

</main>
</body>
</html>
```